Website for new child psychology practice

New clinical psychology practice in NSW Australia, specialising in work with children, adolescents and families. I would like to feature the colours in the logo, which was recently designed by pixelharbor designer Odette.
I am seeking a professional looking page, which is easy to navigate and is colourful and playful but not childish.
Target Market(s)
Parents and professionals
Industry/Entity Type
Health
Coding
Coded - Design and coding required
Number of Pages Required
1 page
Font styles to use
Serif
Requirements
Must have
- Pages for 'About us' 'Services' 'Fees and information' 'Contact us'
Should not have
- Childish stock photos

```html
<!DOCTYPE html>
<html lang="en">
<head>
<meta charset="utf-8">
<title>Dr Clara Hollis — Clinical Psychologist</title>
<link rel="stylesheet" href="https://fonts.googleapis.com/css2?family=Cinzel:wght@400;600;700&family=Poppins:wght@400;500;600&display=swap">
<style>
:root{
  --plum:#7b1d6e;
  --purple:#9c2391;
  --magenta:#b02aa0;
  --pink-card:#c96fb3;
  --orange:#ea7b37;
  --orange-red:#e15a3c;
  --gold:#f5c46c;
  --gold-text:#e8b65a;
  --ink:#1f1a22;
  --text:#3d3640;
  --pale:#f7eaf4;
  --white:#ffffff;
  --black:#0a0a0a;
}
*{margin:0;padding:0;box-sizing:border-box}
html,body{width:1200px;height:3805px;overflow:hidden}
body{position:relative;background:var(--white);font-family:'Poppins',sans-serif;color:var(--text)}
.abs{position:absolute}
.serif{font-family:'Cinzel',serif}

/* top & header */
.top-bar{left:0;top:0;width:1200px;height:4px;background:linear-gradient(90deg,var(--purple),var(--orange),var(--gold),var(--purple))}
.hero{left:0;top:0;width:1200px;height:700px;background:linear-gradient(180deg,#f7e9f3 0%,#f4dcee 100%);overflow:hidden}
.hero-bubble{border-radius:50%;background:rgba(230,190,220,.35)}
.brand{left:100px;top:26px;display:flex;align-items:center;gap:12px}
.brand-dot{width:40px;height:40px;border-radius:50%;background:var(--purple)}
.brand-name{font-family:'Cinzel',serif;font-size:29px;font-weight:600;color:var(--plum);line-height:1}
.brand-sub{font-family:'Cinzel',serif;font-size:11px;letter-spacing:3px;color:var(--plum);margin-top:2px}
.nav{left:476px;top:40px;display:flex;gap:42px;font-family:'Cinzel',serif;font-size:15px;color:var(--ink)}
.nav a{color:inherit;text-decoration:none;position:relative}
.nav a.active::after{content:"";position:absolute;left:25%;right:25%;bottom:-12px;height:2px;background:var(--orange-red)}
.nav-cta{left:918px;top:27px;width:157px;height:44px;border-radius:22px;background:var(--purple);color:#fff;font-family:'Cinzel',serif;font-size:15px;display:flex;align-items:center;justify-content:center}

.hero-line{left:0;top:226px;width:110px;height:2px;background:var(--purple)}
.hero-line::after{content:"";position:absolute;right:0;top:-3px;width:8px;height:8px;background:var(--purple)}
.hero-kicker{left:128px;top:210px;font-size:25px;color:var(--ink)}
.hero-title{left:122px;top:246px;font-family:'Cinzel',serif;font-weight:700;font-size:58px;line-height:54px;letter-spacing:2px}
.hero-title .l1{color:var(--ink)}
.hero-title .l2{color:var(--purple)}
.hero-title .l3{color:var(--orange)}
.hero-btn{left:124px;top:443px;width:270px;height:52px;border-radius:26px;background:linear-gradient(90deg,var(--orange-red),var(--orange));color:#fff;font-family:'Cinzel',serif;font-size:15px;display:flex;align-items:center;padding-left:30px}
.hero-btn-dot{left:354px;top:440px;width:56px;height:56px;border-radius:50%;background:#fff;display:flex;align-items:center;justify-content:center}
.hero-btn-dot span{width:42px;height:42px;border-radius:50%;background:var(--purple)}
.hero-art{left:590px;top:90px}

/* section labels */
.label{font-family:'Cinzel',serif;font-size:21px;letter-spacing:3px}
.heading{font-family:'Cinzel',serif;font-size:44px;letter-spacing:2px;color:var(--ink)}

/* about */
.about-photo{left:95px;top:739px}
.about-label{left:610px;top:802px;color:var(--purple)}
.about-heading{left:610px;top:830px}
.about-line{left:1088px;top:852px;width:112px;height:2px;background:var(--purple)}
.about-line::before{content:"";position:absolute;left:0;top:-3px;width:8px;height:8px;background:var(--purple)}
.about-text{left:615px;top:896px;width:460px;font-size:16px;line-height:27px}
.about-text p+p{margin-top:27px}
.btn{border-radius:25px;color:#fff;font-family:'Cinzel',serif;font-size:15px;display:flex;align-items:center;justify-content:center}
.about-btn{left:607px;top:1112px;width:192px;height:50px;background:linear-gradient(90deg,var(--orange-red),var(--orange))}

/* services */
.services-band{left:0;top:1277px;width:1200px;height:386px;background:linear-gradient(90deg,#7b2468 0%,#9a2a8a 55%,#a42699 100%)}
.services-art{left:560px;top:1277px;width:520px;height:386px;background:radial-gradient(ellipse at center,rgba(255,255,255,.12),rgba(255,255,255,0) 70%)}
.services-label{left:0;width:1200px;top:1338px;text-align:center;color:var(--gold-text);font-size:20px}
.services-heading{left:0;width:1200px;top:1362px;text-align:center;color:#fff;font-size:40px}
.services-rule{left:552px;top:1416px;width:96px;height:1px;background:rgba(255,255,255,.7)}
.services-rule::after{content:"";position:absolute;left:45px;top:-2px;width:5px;height:5px;border-radius:50%;background:var(--gold)}
.card{top:1499px;width:287px;height:233px;color:#fff;text-align:center}
.card-pink{left:146px;background:var(--pink-card)}
.card-plum{left:451px;background:#7a1768}
.card-orange{left:754px;background:var(--orange)}
.card-icon{position:absolute;left:97px;top:-43px;width:92px;height:92px}
.card h3{position:absolute;top:62px;left:0;width:100%;font-family:'Cinzel',serif;font-weight:400;font-size:21px;letter-spacing:1px}
.card p{position:absolute;top:96px;left:40px;width:207px;font-size:11px;line-height:20px}
.card .card-btn{position:absolute;left:72px;top:174px;width:143px;height:36px;border:2px solid var(--gold);border-radius:18px;font-family:'Cinzel',serif;font-size:12px;display:flex;align-items:center;justify-content:center}

/* fees */
.fees-photo{left:517px;top:1744px;width:683px;height:562px;background:linear-gradient(90deg,#ffffff 0%,#e9dfe6 20%,#d9c9c2 55%,#c6a99a 100%)}
.fees-label{left:148px;top:1860px;color:var(--purple)}
.fees-heading{left:146px;top:1888px;font-size:46px}
.fees-rule{left:150px;top:1948px;width:132px;height:1px;background:var(--purple)}
.fees-rule::before{content:"";position:absolute;left:0;top:-3px;width:7px;height:7px;background:var(--purple)}
.fees-text{left:150px;top:1974px;width:364px;font-size:14.5px;line-height:23px;text-align:justify}
.fees-text p+p{margin-top:22px}
.fees-btn{left:151px;top:2158px;width:177px;height:44px;border-radius:22px;background:linear-gradient(90deg,var(--purple),var(--plum))}

/* testimonials */
.testimonials{left:0;top:2306px;width:1200px;height:510px;background:linear-gradient(90deg,#fbeef6 0%,#fcf2ec 60%,#fdf1e3 100%)}
.t-label{left:0;width:1200px;top:2362px;text-align:center;color:var(--purple);font-size:18px}
.t-heading{left:0;width:1200px;top:2382px;text-align:center;font-size:38px;letter-spacing:3px}
.t-card{top:2468px;width:309px;height:251px;background:#fff;border:1.5px solid #d9c7d3;box-shadow:0 4px 10px rgba(0,0,0,.05)}
.t-card p{position:absolute;left:35px;top:32px;width:250px;font-size:13px;line-height:22px}
.t-avatar{position:absolute;left:32px;top:184px;width:38px;height:38px;border-radius:50%;background:linear-gradient(135deg,#d8c2b2,#9b8678)}
.t-name{position:absolute;left:80px;top:186px;font-size:12px;font-weight:600;color:var(--ink)}
.t-stars{position:absolute;left:80px;top:200px;font-size:15px;color:var(--gold);letter-spacing:2px}
.t-badge{position:absolute;right:18px;top:200px;width:26px;height:26px;border-radius:50%;background:#dfe4ea}
.t-arrow{top:2572px}

/* contact */
.contact{left:0;top:2816px;width:1200px;height:595px;background:linear-gradient(100deg,#7b2468 0%,#952877 35%,#c24f5b 65%,#ea7a36 100%);overflow:hidden}
.c-line{left:0;top:2908px;width:107px;height:2px;background:var(--gold)}
.c-line::after{content:"";position:absolute;right:0;top:-3px;width:7px;height:7px;background:var(--gold)}
.c-label{left:143px;top:2896px;color:var(--gold-text);font-size:19px}
.c-heading{left:143px;top:2915px;color:#fff;font-size:38px}
.field{left:143px;width:412px;height:46px;background:#fff;border:1px solid #e7d9e3;font-size:14px;color:var(--ink);padding:14px 20px}
.field-msg{height:92px}
.c-btn{left:143px;top:3256px;width:189px;height:45px;border:2px solid #fff;border-radius:23px;color:#fff;font-size:14px;font-weight:600;display:flex;align-items:center;justify-content:center}
.contact-photo{left:617px;top:2809px}

/* footer */
.footer{left:0;top:3411px;width:1200px;height:394px;background:var(--black)}
.f-divider{top:3411px;width:1px;height:326px;background:#3a3a3a}
.f-brand-dot{left:280px;top:3474px;width:42px;height:42px;border-radius:50%;background:var(--purple)}
.f-brand{left:101px;width:400px;top:3528px;text-align:center;color:#fff}
.f-brand .name{font-family:'Cinzel',serif;font-size:29px;font-weight:600;line-height:1}
.f-brand .sub{font-family:'Cinzel',serif;font-size:11px;letter-spacing:3px;margin-top:2px}
.social{top:3587px;width:48px;height:48px;border-radius:50%;background:var(--purple)}
.f-heading{font-family:'Cinzel',serif;font-size:22px;color:#fff;letter-spacing:1px;border-left:3px solid var(--purple);padding-left:20px;line-height:26px}
.f-links{left:545px;top:3522px;font-size:14px;line-height:27px;color:#fff;list-style:none}
.f-icon{width:44px;height:44px;border-radius:50%;background:var(--purple)}
.f-contact-text{left:832px;font-size:14px;line-height:22px;color:#fff}
.f-bottom-line{left:0;top:3735px;width:1200px;height:3px;background:linear-gradient(90deg,var(--purple),var(--orange),var(--gold),var(--purple))}
.copyright{left:0;width:1200px;top:3760px;text-align:center;font-size:12px;color:#cfcfcf}
</style>
</head>
<body>

<!-- HERO -->
<section class="abs hero" aria-label="Introduction">
  <div class="abs hero-bubble" style="left:-60px;top:140px;width:240px;height:240px"></div>
  <div class="abs hero-bubble" style="left:300px;top:160px;width:200px;height:200px"></div>
  <div class="abs hero-bubble" style="left:150px;top:380px;width:180px;height:180px"></div>
  <div class="abs hero-bubble" style="left:430px;top:380px;width:140px;height:140px"></div>
</section>
<div class="abs top-bar"></div>

<header>
  <div class="abs brand">
    <span class="brand-dot"></span>
    <div>
      <div class="brand-name">Dr Clara Hollis</div>
      <div class="brand-sub">Clinical Psychologist</div>
    </div>
  </div>
  <nav class="abs nav">
    <a href="#about" class="active">About Us</a>
    <a href="#services">Services</a>
    <a href="#fees">Fees &amp; Information</a>
  </nav>
  <a class="abs nav-cta" href="#contact">Contact Us</a>
</header>

<div class="abs hero-line"></div>
<div class="abs hero-kicker serif">Dr Clara Hollis</div>
<h1 class="abs hero-title">
  <span class="l1">Clinical</span><br>
  <span class="l2">Psychology</span><br>
  <span class="l3">Practice</span>
</h1>
<div class="abs hero-btn">Schedule Appointment</div>
<div class="abs hero-btn-dot"><span></span></div>

<svg class="abs hero-art" width="540" height="560" viewBox="0 0 540 560" aria-hidden="false">
  <defs>
    <linearGradient id="heroPurple" x1="0" y1="0" x2="1" y2="1">
      <stop offset="0" stop-color="#d98fd0"/><stop offset="1" stop-color="#8c1c82"/>
    </linearGradient>
    <linearGradient id="heroDuo" x1="0" y1="0" x2="1" y2="1">
      <stop offset="0" stop-color="#d6cfca"/><stop offset="1" stop-color="#6e5e58"/>
    </linearGradient>
    <linearGradient id="heroTeen" x1="0" y1="0" x2="1" y2="1">
      <stop offset="0" stop-color="#c9d2dc"/><stop offset="1" stop-color="#4f6176"/>
    </linearGradient>
  </defs>
  <!-- purple bubble -->
  <path d="M374 154 L250 350 L300 250 Z" fill="#9c2391"/>
  <g role="img" aria-label="Illustration of a head in profile with a tree growing from it over misty hills">
    <circle cx="374" cy="154" r="148" fill="url(#heroPurple)"/>
  </g>
  <!-- two people photo -->
  <path d="M121 225 L230 300 L190 200 Z" fill="#fff"/>
  <g role="img" aria-label="Photo of a man and a teenage boy talking on a sofa">
    <circle cx="121" cy="225" r="103" fill="url(#heroDuo)"/>
  </g>
  <!-- yellow bubble -->
  <path d="M105 402 L205 330 L160 440 Z" fill="#f8c46e"/>
  <circle cx="105" cy="402" r="92" fill="#f8c46e"/>
  <!-- orange bubble -->
  <path d="M343 378 L250 350 L300 420 Z" fill="#dd6a2e"/>
  <circle cx="343" cy="378" r="66" fill="#dd6a2e"/>
  <!-- teen photo -->
  <g role="img" aria-label="Photo of a worried teenage boy with hands clasped">
    <circle cx="251" cy="476" r="76" fill="url(#heroTeen)"/>
  </g>
</svg>

<!-- ABOUT -->
<section id="about" aria-label="About us">
  <svg class="abs about-photo" width="480" height="480" viewBox="0 0 480 480">
    <defs>
      <linearGradient id="aboutPhoto" x1="0" y1="0" x2="1" y2="1">
        <stop offset="0" stop-color="#c9a88e"/><stop offset=".5" stop-color="#e7d5cc"/><stop offset="1" stop-color="#9a8f8c"/>
      </linearGradient>
    </defs>
    <circle cx="236" cy="236" r="236" fill="#f5c46c"/>
    <circle cx="250" cy="240" r="222" fill="#9c2391"/>
    <g role="img" aria-label="Portrait photo of the psychologist smiling with a notebook">
      <circle cx="248" cy="238" r="208" fill="url(#aboutPhoto)"/>
    </g>
  </svg>
  <h2 class="abs label about-label">About Us</h2>
  <div class="abs heading about-heading">Dr Clara Hollis</div>
  <div class="abs about-line"></div>
  <div class="abs about-text">
    <p>Lorem ipsum dolor sit amet, consectetur adipiscing elit, sed do eiusmod tempor incididunt ut labore et dolore magna aliqua. Quis ipsum suspendisse ultrices gravida. Risus commodo viverra maecenas accumsa</p>
    <p>Lorem ipsum dolor sit amet, consectetur adipiscing elit, sed do eiusmod tempor incididunt ut labore et dolore</p>
  </div>
  <a class="abs btn about-btn">Learn More</a>
</section>

<!-- SERVICES -->
<section id="services" aria-label="Services">
  <div class="abs services-band"></div>
  <div class="abs services-art" role="img" aria-label="Faint tree illustration in the background"></div>
  <div class="abs label services-label">What We Do</div>
  <h2 class="abs heading services-heading">Services Provide</h2>
  <div class="abs services-rule"></div>

  <article class="abs card card-pink">
    <svg class="card-icon" viewBox="0 0 92 92"><path d="M46 4a42 42 0 1 1-30 71l-12 13 6-22A42 42 0 0 1 46 4z" fill="#8d1d80"/><circle cx="46" cy="44" r="20" fill="none" stroke="#fff" stroke-width="2"/><path d="M38 44h16M46 36v16" stroke="#fff" stroke-width="2"/></svg>
    <h3>Services Heading</h3>
    <p>Lorem ipsum dolor sit amet, consectetur adipiscing elit, sed do eiusmod toLorem ipsum dolor sit</p>
    <span class="card-btn">Learn More</span>
  </article>
  <article class="abs card card-plum">
    <svg class="card-icon" viewBox="0 0 92 92"><path d="M46 4a42 42 0 1 1-30 71l-12 13 6-22A42 42 0 0 1 46 4z" fill="#ea7b37"/><circle cx="46" cy="44" r="20" fill="none" stroke="#fff" stroke-width="2"/><circle cx="46" cy="44" r="6" fill="#fff"/></svg>
    <h3>Services Heading</h3>
    <p>Lorem ipsum dolor sit amet, consectetur adipiscing elit, sed do eiusmod toLorem ipsum dolor sit</p>
    <span class="card-btn">Learn More</span>
  </article>
  <article class="abs card card-orange">
    <svg class="card-icon" viewBox="0 0 92 92"><path d="M46 4a42 42 0 1 1-30 71l-12 13 6-22A42 42 0 0 1 46 4z" fill="#f5c46c"/><circle cx="46" cy="44" r="20" fill="none" stroke="#fff" stroke-width="2"/><path d="M36 48q10-14 20 0" fill="none" stroke="#fff" stroke-width="2"/></svg>
    <h3>Services Heading</h3>
    <p>Lorem ipsum dolor sit amet, consectetur adipiscing elit, sed do eiusmod toLorem ipsum dolor sit</p>
    <span class="card-btn">Learn More</span>
  </article>
</section>

<!-- FEES -->
<section id="fees" aria-label="Fees and information">
  <div class="abs fees-photo" role="img" aria-label="Photo of a smiling psychologist with a clipboard talking with a young girl"></div>
  <h2 class="abs label fees-label">Fee &amp; Information</h2>
  <div class="abs heading fees-heading">Our Fees</div>
  <div class="abs fees-rule"></div>
  <div class="abs fees-text">
    <p>Lorem ipsum dolor sit amet, consectetur adipiscing elit, sed do eiusmod tempor incididunt ut labore</p>
    <p>At dolore magna aliqua. Quis ipsum suspendisse ultrices Lorem ipsum dolor sit amet, consectetur adipiscing elit, sed do eiusmod tempor incididunt ut labore et dolore ultrices Lorem ipsum dolor sit</p>
  </div>
  <a class="abs btn fees-btn">Learn More</a>
</section>

<!-- TESTIMONIALS -->
<section aria-label="Testimonials">
  <div class="abs testimonials"></div>
  <div class="abs label t-label">People Words</div>
  <h2 class="abs heading t-heading">Testimonials</h2>

  <svg class="abs t-arrow" style="left:78px" width="22" height="36" viewBox="0 0 22 36"><path d="M18 3 4 18l14 15" fill="none" stroke="#c96fb3" stroke-width="3"/></svg>
  <svg class="abs t-arrow" style="left:1132px" width="22" height="36" viewBox="0 0 22 36"><path d="M4 3l14 15L4 33" fill="none" stroke="#c96fb3" stroke-width="3"/></svg>

  <article class="abs t-card" style="left:127px">
    <p>Lorem ipsum dolor sit amet, consectetur adipiscing elit, sed do eiusmod tempor incididunt ut labore et dolore magna aliqua. Quis ipsum suspendisse ultrices gravida. Risus commodo viverra maecenas acc</p>
    <span class="t-avatar" role="img" aria-label="Reviewer photo"></span>
    <span class="t-name">Daniel Brooks</span>
    <span class="t-stars">★★★★★</span>
    <span class="t-badge" aria-label="Review source"></span>
  </article>
  <article class="abs t-card" style="left:460px">
    <p>Lorem ipsum dolor sit amet, consectetur adipiscing elit, sed do eiusmod tempor incididunt ut labore et dolore magna aliqua. Quis ipsum suspendisse ultrices gravida. Risus commodo viverra maecenas acc</p>
    <span class="t-avatar" role="img" aria-label="Reviewer photo"></span>
    <span class="t-name">Daniel Brooks</span>
    <span class="t-stars">★★★★★</span>
    <span class="t-badge" aria-label="Review source"></span>
  </article>
  <article class="abs t-card" style="left:792px">
    <p>Lorem ipsum dolor sit amet, consectetur adipiscing elit, sed do eiusmod tempor incididunt ut labore et dolore magna aliqua. Quis ipsum suspendisse ultrices gravida. Risus commodo viverra maecenas acc</p>
    <span class="t-avatar" role="img" aria-label="Reviewer photo"></span>
    <span class="t-name">Daniel Brooks</span>
    <span class="t-stars">★★★★★</span>
    <span class="t-badge" aria-label="Review source"></span>
  </article>
</section>

<!-- CONTACT -->
<section id="contact" aria-label="Contact us">
  <div class="abs contact"></div>
  <div class="abs c-line"></div>
  <div class="abs label c-label">Get In Touch</div>
  <h2 class="abs heading c-heading">Contact Us</h2>
  <div class="abs field" style="top:2985px">Name*</div>
  <div class="abs field" style="top:3039px">Email address*</div>
  <div class="abs field" style="top:3094px">Subject*</div>
  <div class="abs field field-msg" style="top:3150px">Message</div>
  <a class="abs c-btn">SEND MESSAGE</a>
  <svg class="abs contact-photo" width="480" height="480" viewBox="0 0 480 480">
    <defs>
      <linearGradient id="familyPhoto" x1="0" y1="0" x2="1" y2="1">
        <stop offset="0" stop-color="#e9e4df"/><stop offset=".5" stop-color="#cdbfb3"/><stop offset="1" stop-color="#7b93b6"/>
      </linearGradient>
    </defs>
    <circle cx="236" cy="236" r="236" fill="#f5c46c"/>
    <circle cx="242" cy="242" r="222" fill="#9c2391"/>
    <g role="img" aria-label="Photo of a smiling father, mother and daughter together at a table">
      <circle cx="236" cy="236" r="210" fill="url(#familyPhoto)"/>
    </g>
  </svg>
</section>

<!-- FOOTER -->
<footer aria-label="Footer">
  <div class="abs footer"></div>
  <div class="abs f-divider" style="left:505px"></div>
  <div class="abs f-divider" style="left:752px"></div>
  <div class="abs f-brand-dot"></div>
  <div class="abs f-brand">
    <div class="name">Dr Clara Hollis</div>
    <div class="sub">Clinical Psychologist</div>
  </div>
  <span class="abs social" style="left:217px" aria-label="Social link"></span>
  <span class="abs social" style="left:267px" aria-label="Social link"></span>
  <span class="abs social" style="left:317px" aria-label="Social link"></span>

  <div class="abs f-heading" style="left:505px;top:3480px">Quick Links</div>
  <ul class="abs f-links">
    <li>Home</li><li>About Us</li><li>Services</li><li>Fees &amp; Information</li><li>Contact Us</li>
  </ul>

  <div class="abs f-heading" style="left:752px;top:3480px">Contact Us</div>
  <span class="abs f-icon" style="left:778px;top:3527px"></span>
  <svg class="abs" style="left:789px;top:3538px" width="22" height="22" viewBox="0 0 24 24"><path d="M6.6 10.8a15 15 0 0 0 6.6 6.6l2.2-2.2c.3-.3.7-.4 1-.2 1.1.4 2.3.6 3.6.6.6 0 1 .4 1 1V20c0 .6-.4 1-1 1A17 17 0 0 1 3 4c0-.6.4-1 1-1h3.5c.6 0 1 .4 1 1 0 1.3.2 2.5.6 3.6.1.3 0 .7-.2 1z" fill="#fff"/></svg>
  <div class="abs f-contact-text" style="top:3526px">Phone Number<br><strong>(02) 5550 1427</strong></div>
  <span class="abs f-icon" style="left:778px;top:3596px"></span>
  <svg class="abs" style="left:789px;top:3609px" width="22" height="18" viewBox="0 0 22 18"><rect x="1" y="1" width="20" height="16" rx="2" fill="#fff"/><path d="M1 3l10 7 10-7" fill="none" stroke="#9c2391" stroke-width="2"/></svg>
  <div class="abs f-contact-text" style="top:3596px">Email address<br>hello@clarahollis.example</div>

  <div class="abs f-bottom-line"></div>
  <div class="abs copyright">© 2024 Dr Clara Hollis. All Rights Reserved</div>
</footer>

</body>
</html>
```